Brindle Yard Care. The best in the biz

I run a lawn care service that offers full service mowing. 100% satisfaction guarantee. Fast, Friendly, quality service "I am your lawns best friend" I cut residential lawns. I offer a mow package that includes trimming, edging and clean up. Prices very from 20 dollars to 75. I want my logo to stand out. Free estimates

Target Market(s)

Home owners

Industry/Entity Type

Landscaping

Contact Information for Business Card

555-812-4473 tomvale48@quillmail.net Derek. Brindle Yard care

Colors
f37122
9bcb3c
cadf82

Requirements
Must have
• Company name.
• Phone number
• Email
• My services
• images
Nice to have
• A sun that is growing grass.
Should not have
• Incorrect information

```html
<!DOCTYPE html>
<html lang="en">
<head>
<meta charset="UTF-8">
<title>Brindle Yard Care — Business Card</title>
<link rel="stylesheet" href="https://fonts.googleapis.com/css2?family=Montserrat:wght@600&family=Open+Sans:wght@400;700&display=swap">
<style>
  :root {
    --page-bg: #e9e9e7;
    --card-bg: #fbfbfa;
    --brand-green: #129a43;
    --brand-orange: #f08a1e;
    --wave-silver: #d9d9d9;
    --text-light: #ffffff;
  }
  * { box-sizing: border-box; margin: 0; padding: 0; }
  html, body {
    width: 1200px;
    height: 900px;
    overflow: hidden;
    background: var(--page-bg);
  }
  .business-card {
    position: absolute;
    left: 120px;
    top: 153px;
    width: 960px;
    height: 594px;
    background: var(--card-bg);
    overflow: hidden;
    box-shadow: 0 10px 30px rgba(0,0,0,0.12);
  }
  .card-wave {
    position: absolute;
    inset: 0;
    width: 960px;
    height: 594px;
  }
  .brand {
    position: absolute;
    left: 60px;
    top: 272px;
    display: flex;
    align-items: center;
    gap: 16px;
  }
  .brand-dot {
    width: 40px;
    height: 40px;
    border-radius: 50%;
    background: var(--brand-orange);
  }
  .brand-name {
    font-family: "Montserrat", sans-serif;
    font-weight: 600;
    font-size: 50px;
    letter-spacing: 0.5px;
    color: var(--brand-green);
    line-height: 1;
  }
  .contact {
    position: absolute;
    right: 63px;
    top: 390px;
    text-align: right;
    font-family: "Open Sans", sans-serif;
    color: var(--text-light);
  }
  .contact-name {
    font-weight: 700;
    font-size: 31px;
    margin-bottom: 28px;
  }
  .contact-line {
    display: flex;
    justify-content: flex-end;
    align-items: center;
    gap: 16px;
    font-size: 23px;
    line-height: 1;
    margin-bottom: 18px;
  }
  .contact-icon {
    width: 20px;
    height: 20px;
    flex: none;
  }
</style>
</head>
<body>
  <div class="business-card">
    <svg class="card-wave" viewBox="0 0 960 594" aria-hidden="true">
      <path d="M0 398 C 150 470, 260 530, 420 490 C 600 440, 800 318, 960 340"
            fill="none" stroke="var(--brand-orange)" stroke-width="9"/>
      <path d="M0 408 C 150 480, 260 540, 420 500 C 600 450, 800 330, 960 352 L960 594 L0 594 Z"
            fill="var(--wave-silver)"/>
      <path d="M0 415 C 150 487, 260 547, 420 507 C 600 457, 800 337, 960 359 L960 594 L0 594 Z"
            fill="var(--brand-green)"/>
    </svg>

    <div class="brand">
      <span class="brand-dot"></span>
      <span class="brand-name">Brindle Yard Care</span>
    </div>

    <div class="contact">
      <p class="contact-name">Derek</p>
      <p class="contact-line">
        <span>555-812-4473</span>
        <svg class="contact-icon" viewBox="0 0 24 24" aria-label="Phone">
          <path fill="#fff" d="M6.6 10.8a15.1 15.1 0 0 0 6.6 6.6l2.2-2.2c.3-.3.7-.4 1-.2 1.1.4 2.3.6 3.6.6.6 0 1 .4 1 1V20c0 .6-.4 1-1 1A17 17 0 0 1 3 4c0-.6.4-1 1-1h3.5c.6 0 1 .4 1 1 0 1.3.2 2.5.6 3.6.1.3 0 .7-.2 1z"/>
        </svg>
      </p>
      <p class="contact-line">
        <span>tomvale48@quillmail.net</span>
        <svg class="contact-icon" viewBox="0 0 24 24" aria-label="Email">
          <rect x="2" y="5" width="20" height="14" fill="#fff"/>
          <path d="M2 5 L12 13 L22 5" fill="none" stroke="var(--brand-green)" stroke-width="1.8"/>
        </svg>
      </p>
    </div>
  </div>
</body>
</html>
```